Veldmark Supplies Business Card

Professional business card that stand out to our potential customers. Front and back with clean modern design

Industry/Entity Type

Oil and gas

Contact Information for Business Card

Name, address, website , office phone and cell number

Requirements
Must have
• Editable files for each employee

```html
<!DOCTYPE html>
<html lang="en">
<head>
<meta charset="utf-8">
<title>Veldmark Supplies Business Card</title>
<link rel="stylesheet" href="https://fonts.googleapis.com/css2?family=Montserrat:wght@500;600;800&display=swap">
<style>
  :root {
    --brand-red: #ec2127;
    --brand-blue: #0bafd3;
    --ink: #1a1a1a;
    --paper: #ffffff;
    --backdrop: #2b2b2b;
  }
  * { box-sizing: border-box; margin: 0; padding: 0; }
  html, body { width: 1200px; height: 880px; overflow: hidden; }
  body {
    background: var(--backdrop);
    font-family: "Montserrat", Arial, sans-serif;
    position: relative;
  }
  .card {
    position: absolute;
    left: 320px;
    width: 560px;
    height: 320px;
    overflow: hidden;
  }
  .card-front { top: 90px; background: var(--brand-red); }
  .card-back { top: 470px; background: var(--paper); }

  .front-wordmark {
    position: absolute;
    inset: 0;
    display: flex;
    align-items: center;
    justify-content: center;
    gap: 14px;
  }
  .front-wordmark .mark-square {
    width: 30px; height: 30px; background: var(--paper);
  }
  .front-wordmark .name {
    color: var(--paper);
    font-weight: 800;
    font-size: 30px;
    letter-spacing: 2px;
    text-transform: uppercase;
  }

  .back-wordmark {
    position: absolute;
    left: 36px;
    top: 90px;
    width: 210px;
    display: flex;
    flex-direction: column;
    align-items: center;
    gap: 12px;
  }
  .back-wordmark .mark-square {
    width: 54px; height: 54px; background: var(--brand-red);
  }
  .back-wordmark .name {
    color: var(--brand-red);
    font-weight: 800;
    font-size: 19px;
    letter-spacing: 1px;
    text-transform: uppercase;
    text-align: center;
  }

  .divider-lines { position: absolute; left: 232px; top: 56px; }

  .contact {
    position: absolute;
    left: 300px;
    top: 40px;
    color: var(--ink);
  }
  .contact .person {
    color: var(--brand-red);
    font-weight: 800;
    font-size: 20px;
    letter-spacing: .5px;
    text-transform: uppercase;
  }
  .contact .role { font-size: 12px; font-weight: 500; margin-bottom: 10px; }
  .contact .address { font-size: 11.5px; font-weight: 500; line-height: 1.35; margin-bottom: 10px; }
  .contact-list { list-style: none; }
  .contact-list li {
    display: flex; align-items: center; gap: 8px;
    font-size: 11.5px; font-weight: 500; margin-bottom: 5px;
  }
  .contact-list .icon {
    width: 15px; height: 15px; background: var(--brand-red);
    border-radius: 2px; display: flex; align-items: center; justify-content: center;
  }
  .contact-list .accent { color: var(--brand-red); }

  .wave-band { position: absolute; left: 0; bottom: 0; }
</style>
</head>
<body>

<section class="card card-front" aria-label="Card front">
  <div class="front-wordmark">
    <span class="mark-square"></span>
    <span class="name">Veldmark Supplies</span>
  </div>
</section>

<section class="card card-back" aria-label="Card back">
  <div class="back-wordmark">
    <span class="mark-square"></span>
    <span class="name">Veldmark Supplies</span>
  </div>

  <svg class="divider-lines" width="50" height="170" viewBox="0 0 50 170">
    <line x1="4" y1="0" x2="46" y2="168" stroke="var(--brand-blue)" stroke-width="1.5"/>
    <line x1="20" y1="28" x2="44" y2="124" stroke="var(--brand-red)" stroke-width="1.5"/>
    <line x1="6" y1="48" x2="28" y2="136" stroke="var(--brand-red)" stroke-width="1.5"/>
  </svg>

  <div class="contact">
    <p class="person">Dalen Ashworth</p>
    <p class="role">President</p>
    <p class="address">2740 Harlow Ave, Ste<br>100, Dalton, TX 75590</p>
    <ul class="contact-list">
      <li><span class="icon"><svg width="9" height="9" viewBox="0 0 10 10"><path d="M2 1 L4 1 L4.5 3 L3.3 3.8 Q4.3 5.8 6.2 6.7 L7 5.5 L9 6 L9 8 Q5 9 2 6 Q0.8 3.5 2 1Z" fill="#fff"/></svg></span>555-204-3187</li>
      <li><span class="icon"><svg width="9" height="9" viewBox="0 0 10 10"><rect x="2.5" y="0.5" width="5" height="9" rx="1" fill="#fff"/><rect x="3.3" y="1.5" width="3.4" height="6" fill="var(--brand-red)"/></svg></span>000-000-9999</li>
      <li><span class="icon"><svg width="10" height="8" viewBox="0 0 10 8"><rect x="0.5" y="0.5" width="9" height="7" fill="none" stroke="#fff"/><path d="M0.5 0.5 L5 4.5 L9.5 0.5" fill="none" stroke="#fff"/></svg></span>info@example-youremail.com</li>
      <li><span class="icon"><svg width="9" height="9" viewBox="0 0 10 10"><circle cx="5" cy="5" r="4.2" fill="none" stroke="#fff"/><line x1="0.8" y1="5" x2="9.2" y2="5" stroke="#fff" stroke-width=".8"/><ellipse cx="5" cy="5" rx="1.8" ry="4.2" fill="none" stroke="#fff" stroke-width=".8"/></svg></span>www.<span class="accent">example-yourwebsite</span>.com</li>
    </ul>
  </div>

  <svg class="wave-band" width="560" height="130" viewBox="0 0 560 130" preserveAspectRatio="none">
    <path d="M0 100 C120 40 260 70 380 60 C460 52 520 20 560 0 L560 130 L0 130 Z" fill="var(--brand-blue)"/>
    <path d="M0 112 C130 60 270 86 390 74 C470 66 525 36 560 18 L560 130 L0 130 Z" fill="var(--paper)"/>
    <path d="M0 116 C130 66 270 92 390 80 C470 72 525 42 560 24 L560 130 L0 130 Z" fill="var(--brand-red)"/>
  </svg>
</section>

</body>
</html>
```